Dovecote Realty

Business cards for 4 people

They need to say for all
87 Tarrow Quay, Boston MA 02114

Each person will have their own personal information
We would like gold embossing for the name of the company
Marla is the blonde sitting in the chair smiling her information should be on the back of the card with her name and information
Should say for slogan classic pattern, elevated experience
marla@dovecoteprops.com
(413) 555-0182

Odette is the brunette with wavy hair in the tan suit celina@dovecoteprops.com
(617) 555-0137

faith@dovecoteprops.com
(413) 555-0164
standing next to the chair

hope@dovecoteprops.com
(413) 555-0199
close up headshot

```html
<!DOCTYPE html>
<html lang="en">
<head>
<meta charset="utf-8">
<title>Dovecote Realty Business Card</title>
<link rel="stylesheet" href="https://fonts.googleapis.com/css2?family=Cinzel:wght@500&family=Libre+Baskerville:wght@700&family=Montserrat:wght@400&display=swap">
<style>
  :root {
    --backdrop: #1b1b1c;
    --card-navy: #213354;
    --gold: #e3b35e;
    --ivory: #f2f2f0;
    --photo-top: #2a3a5a;
    --photo-bottom: #1a1f2b;
  }
  * { margin: 0; padding: 0; box-sizing: border-box; }
  html, body { width: 1200px; height: 1059px; overflow: hidden; background: var(--backdrop); }
  .stage { position: relative; width: 1200px; height: 1059px; }

  .card {
    position: absolute;
    background: var(--card-navy);
    border-radius: 18px;
    overflow: hidden;
  }
  .card--front { left: 257px; top: 89px; width: 687px; height: 390px; }
  .card--back  { left: 254px; top: 547px; width: 693px; height: 393px; }

  .brand { position: absolute; text-align: center; }
  .brand-circle { display: block; margin: 0 auto; }
  .brand-name {
    font-family: "Cinzel", serif;
    font-weight: 500;
    color: var(--gold);
    white-space: nowrap;
    letter-spacing: 0.02em;
    line-height: 1.1;
  }
  .card--front .brand { left: 37px; top: 38px; width: 206px; }
  .card--front .brand-name { font-size: 20px; margin-top: 10px; }
  .card--back .brand { left: 0; top: 90px; width: 693px; }
  .card--back .brand-name { font-size: 38px; margin-top: 12px; }

  .accent-bar { position: absolute; left: 0; top: 191px; width: 17px; height: 41px; background: var(--gold); }
  .agent-name {
    position: absolute; left: 37px; top: 188px;
    font-family: "Libre Baskerville", serif; font-weight: 700;
    font-size: 21px; color: var(--gold); letter-spacing: 0.01em;
  }
  .agent-title {
    position: absolute; left: 37px; top: 216px;
    font-family: "Montserrat", sans-serif; font-size: 16.5px;
    color: var(--ivory); letter-spacing: 0.02em;
  }
  .contact-list { position: absolute; left: 37px; top: 256px; list-style: none; }
  .contact-item {
    display: flex; align-items: center; height: 25px;
    font-family: "Montserrat", sans-serif; font-size: 16.5px;
    color: var(--ivory); letter-spacing: 0.02em;
  }
  .contact-icon { width: 13px; height: 13px; margin-right: 6px; fill: var(--gold); flex: none; }

  .agent-photo {
    position: absolute; left: 432px; top: 34px; width: 255px; height: 356px;
    background: linear-gradient(180deg, var(--photo-top), var(--photo-bottom));
  }
</style>
</head>
<body>
<main class="stage">

  <section class="card card--front">
    <div class="brand">
      <svg class="brand-circle" width="74" height="74" viewBox="0 0 74 74" aria-hidden="true">
        <circle cx="37" cy="37" r="34" fill="none" stroke="var(--gold)" stroke-width="3"/>
      </svg>
      <div class="brand-name">DOVECOTE REALTY</div>
    </div>

    <div class="accent-bar"></div>
    <h1 class="agent-name">MARLA WHITCOMBE</h1>
    <p class="agent-title">Real Estate Advisor and Rentals Manager</p>

    <ul class="contact-list">
      <li class="contact-item">
        <svg class="contact-icon" viewBox="0 0 24 24" aria-hidden="true"><path d="M6.6 10.8a15.1 15.1 0 0 0 6.6 6.6l2.2-2.2a1 1 0 0 1 1-.25 11.4 11.4 0 0 0 3.6.57 1 1 0 0 1 1 1V20a1 1 0 0 1-1 1A17 17 0 0 1 3 4a1 1 0 0 1 1-1h3.5a1 1 0 0 1 1 1c0 1.25.2 2.45.57 3.57a1 1 0 0 1-.25 1z"/></svg>
        (413) 555-0182
      </li>
      <li class="contact-item">
        <svg class="contact-icon" viewBox="0 0 24 24" aria-hidden="true"><path d="M2 9l10-6 10 6v12H2zm2 1.2V19h16v-8.8l-8 5z"/></svg>
        marla@dovecoteprops.com
      </li>
      <li class="contact-item">
        <svg class="contact-icon" viewBox="0 0 24 24" aria-hidden="true"><circle cx="12" cy="12" r="10"/></svg>
        www.dovecoteprops.com
      </li>
      <li class="contact-item">
        <svg class="contact-icon" viewBox="0 0 24 24" aria-hidden="true"><path d="M12 1a8 8 0 0 0-8 8c0 6 8 14 8 14s8-8 8-14a8 8 0 0 0-8-8zm0 11a3 3 0 1 1 0-6 3 3 0 0 1 0 6z"/></svg>
        87 Tarrow Quay, Boston MA 02114
      </li>
    </ul>

    <div class="agent-photo" role="img" aria-label="Portrait of the agent in a black suit seated on a wooden chair"></div>
  </section>

  <section class="card card--back">
    <div class="brand">
      <svg class="brand-circle" width="136" height="136" viewBox="0 0 136 136" aria-hidden="true">
        <circle cx="68" cy="68" r="65" fill="none" stroke="var(--gold)" stroke-width="4"/>
      </svg>
      <div class="brand-name">DOVECOTE REALTY</div>
    </div>
  </section>

</main>
</body>
</html>
```